PlayTallyCollective - Game Statistics and Achievement Tracking

I need a new modern design for an existing website.

The website is a project to track statistics and achievements for games (currently Vaporn Achievements/Stats and stats for Cargo Haul Odyssey 2 and Frontier Rig Journeys).
I am currently expanding the site with other platforms (like QVR) and more games.
I am also adding a user registration/signin with user profiles to show off their achievements and stats across all platforms and games.

The current website is available at https://plytly.example/
To search for data you can use the username "pixelornin" (without quotes).

The design should be modern and extendable and contain space for a logo.

The logo should match the project. It should combine Gaming with statistics.

Target Market(s)

Video game players

Number of Pages Required

5+ page

Font styles to use
Sans Serif

Requirements
Must have
• Basic Layout, User profile page (not yet available on live site), Search Page for Platforms/Games, Platform profile page, Dark theme

```html
<!DOCTYPE html>
<html lang="en">
<head>
<meta charset="utf-8">
<title>PlayTally – Game Statistics</title>
<link rel="stylesheet" href="https://fonts.googleapis.com/css2?family=Audiowide&family=Roboto:wght@400;500&display=swap">
<style>
:root{
  --bg:#1b0b58;
  --bg-deep:#12063d;
  --panel:#0d0533;
  --tile:#2c14a6;
  --tile-2:#3519c0;
  --violet:#5c35f2;
  --violet-soft:#7a55ff;
  --red:#e0192d;
  --red-dark:#5b0a1e;
  --white:#ffffff;
  --muted:#a99ae6;
  --display:'Audiowide', sans-serif;
  --body:'Roboto', sans-serif;
}
*{box-sizing:border-box;margin:0;padding:0}
html,body{width:1200px;height:3473px;overflow:hidden}
body{background:linear-gradient(180deg,var(--bg) 0,#1e0d63 40%,#1c0b5e 85%,var(--bg-deep) 100%);color:var(--white);font-family:var(--body);position:relative}
.abs{position:absolute}
/* header */
.site-header{position:absolute;left:0;top:0;width:1200px;height:60px;z-index:5;background:rgba(20,6,60,.35)}
.brand{position:absolute;left:139px;top:16px}
.brand-name{font-family:var(--display);font-size:22px;color:var(--violet-soft);letter-spacing:1px;line-height:1}
.brand-tag{font-family:var(--display);font-size:8px;color:var(--white);margin-top:4px;letter-spacing:.2px}
.main-nav a{position:absolute;top:22px;font-family:var(--display);font-size:12px;color:var(--white);text-decoration:none}
.main-nav a.active{color:var(--red)}
.btn-login,.btn-register{position:absolute;top:0;height:60px;font-family:var(--display);font-size:13px;display:flex;align-items:center;justify-content:center;color:var(--white)}
.btn-login{left:851px;width:80px;background:var(--red-dark)}
.btn-register{left:933px;width:129px;background:#35199e}
/* hero */
.hero-art{position:absolute;left:0;top:0;width:1200px;height:505px;background:radial-gradient(ellipse at 50% 30%,#4a2db5 0,#2a137a 45%,#1b0b58 80%);clip-path:path('M0 0 H1200 V395 Q600 560 0 395 Z')}
.hero-title{position:absolute;left:0;top:196px;width:1200px;text-align:center;font-family:var(--display);font-size:56px;color:var(--violet);letter-spacing:3px;line-height:1}
.hero-sub{position:absolute;left:0;top:266px;width:1200px;text-align:center;font-family:var(--display);font-size:9px}
.search{position:absolute;left:173px;top:321px;width:857px;height:43px;background:rgba(28,10,72,.85);display:flex;align-items:center}
.search span{font-family:var(--display);font-size:11px;padding-left:13px;flex:1}
.search .go{width:66px;height:43px;background:#3b1ab8;display:flex;align-items:center;justify-content:center}
/* section titles */
.section-title{position:absolute;left:0;width:1200px;text-align:center;font-family:var(--display);font-size:16px;color:#4e2ae0;display:flex;justify-content:center;align-items:center;gap:18px}
.section-title::before,.section-title::after{content:"";width:9px;height:9px;border-radius:50%;background:#5c3af5;box-shadow:0 0 10px 4px #3a1ad0}
/* intro */
.intro-photo{position:absolute;left:0;top:619px;width:586px;height:207px;background:linear-gradient(110deg,#150738,#3a1a8a 55%,#7c2fa8);clip-path:polygon(0 0,500px 0,586px 103px,500px 207px,0 207px)}
.intro-text{position:absolute;left:607px;top:634px;width:430px;font-size:12.5px;line-height:17px;color:#8f7fd6}
.intro-text p{margin-bottom:17px}
/* profile */
.profile-card{position:absolute;left:115px;top:1053px;width:970px;height:360px;border:2px solid #3a1bc0;background:var(--panel)}
.profile-side{position:absolute;right:0;top:0;width:63px;height:299px;background:#1c0b66}
.profile-side svg{position:absolute;left:21px}
.avatar-main{position:absolute;left:45px;top:37px;width:176px;height:176px;border-radius:50%;background:radial-gradient(circle,#c8a978 0,#6a4aa0 70%,#2d1a8a 100%);border:4px solid #4b2de0}
.stat-row{position:absolute;left:269px;font-size:14px}
.stat-row .k{position:absolute;left:0;color:var(--violet);white-space:nowrap}
.stat-row .v{position:absolute;left:138px;color:var(--white);white-space:nowrap}
.profile-foot{position:absolute;left:0;top:299px;width:966px;height:57px;border-top:2px solid #2a1490;font-size:14px}
.profile-foot span{position:absolute;top:18px;white-space:nowrap}
.pf-k{color:var(--violet)}
.pf-v{color:var(--white);font-weight:500}
.friend{position:absolute;top:1445px;width:131px;height:155px;border:2px solid #2a1490;background:linear-gradient(180deg,#160845,#0d0533)}
/* stats */
.stat-tile{position:absolute;width:316px;height:115px;background:linear-gradient(135deg,var(--tile-2),var(--tile))}
.stat-tile .label{position:absolute;left:34px;top:28px;font-size:16px}
.stat-tile .num{position:absolute;left:28px;top:58px;font-family:var(--display);font-size:38px;color:#6f4bff;line-height:1;letter-spacing:1px}
.stat-tile .sub{position:absolute;left:28px;top:94px;font-size:15px}
.stat-tile svg{position:absolute}
/* games */
.game{position:absolute;width:164px;height:173px;border-radius:14px;display:flex;align-items:center;justify-content:center;text-align:center;font-family:var(--display);font-size:15px;line-height:18px;padding:0 14px;text-transform:uppercase}
.loading{position:absolute;left:0;top:2931px;width:1200px;text-align:center;font-family:var(--display);font-size:16px;letter-spacing:3px}
/* footer */
.footer-glow{position:absolute;left:0;top:3080px;width:1200px;height:393px;background:radial-gradient(ellipse at 50% 20%,#2d148a 0,#1a0a54 55%,var(--bg-deep) 100%)}
.foot-brand{position:absolute;left:0;top:3186px;width:1200px;text-align:center}
.foot-brand .brand-name{font-size:22px}
.foot-nav{position:absolute;left:0;top:3263px;width:1200px;display:flex;justify-content:center;gap:30px;font-family:var(--display);font-size:12px}
.foot-nav .active{color:var(--red)}
.social{position:absolute;left:0;top:3322px;width:1200px;display:flex;justify-content:center;gap:36px;font-size:13px;font-weight:500}
.copyright{position:absolute;left:0;top:3378px;width:1200px;text-align:center;font-size:11px;letter-spacing:2px}
.version{position:absolute;left:1030px;top:3372px;font-size:10px;letter-spacing:1px}
</style>
</head>
<body>

<div class="hero-art" role="img" aria-label="Dashboard artwork with speedometer gauges, charts and neon game data panels"></div>

<header class="site-header">
  <div class="brand"><div class="brand-name">PLAYTALLY</div><div class="brand-tag">PLAYTALLYCOLLECTIVE</div></div>
  <nav class="main-nav">
    <a class="active" style="left:550px">HOME</a>
    <a style="left:620px">VAPORN</a>
    <a style="left:710px">GAMES</a>
    <a style="left:790px">ABOUT</a>
  </nav>
  <div class="btn-login">LOGIN</div>
  <div class="btn-register">REGISTER</div>
</header>

<div class="hero-title">PLAYTALLY</div>
<div class="hero-sub">PLAYTALLYCOLLECTIVE</div>
<div class="search"><span>SEARCH PLATFORMS/GAMES</span><div class="go"><svg width="12" height="12" viewBox="0 0 12 12"><circle cx="5" cy="5" r="3.6" fill="none" stroke="#fff" stroke-width="1.8"/><line x1="7.6" y1="7.6" x2="11" y2="11" stroke="#fff" stroke-width="1.8"/></svg></div></div>

<div class="section-title" style="top:562px">PLAYTALLYCOLLECTIVE</div>
<div class="intro-photo" role="img" aria-label="Photo of friends cheering while playing video games"></div>
<div class="intro-text">
  <p>Welcome to the PlayTallyCollective!</p>
  <p>We offer you free and easy insights into your game statistics and achievements on multiple platforms and games.</p>
  <p>If you want to learn more about us visit our about us page, otherwise go ahead and try our service!</p>
  <p>This page is under constant construction and we are trying to add more stats, games and platforms over time, so stay tuned.</p>
</div>

<div class="section-title" style="top:970px">ACHIEVEMENTS</div>
<section class="profile-card">
  <div class="avatar-main" role="img" aria-label="Profile avatar illustration"></div>
  <div class="stat-row" style="top:50px"><span class="k">PLAYED GAMES:</span><span class="v">1166 / 1644 (70%)</span></div>
  <div class="stat-row" style="top:88px"><span class="k">TOTAL PLAY TIME:</span><span class="v">1 YEAR 2 MONTHS 11 HOURS 25 MINUTES</span></div>
  <div class="stat-row" style="top:126px"><span class="k">ACHIEVEMENTS:</span><span class="v">18007 / 63070 (28%)</span></div>
  <div class="stat-row" style="top:165px"><span class="k">MEMBER SINCE:</span><span class="v">14.01.2009</span></div>
  <div class="stat-row" style="top:202px"><span class="k">LAST PLAYED:</span><span class="v">RAIL RIDE WORLD 5</span></div>
  <div class="stat-row" style="top:241px"><span class="k">LAST UPDATE:</span><span class="v">26.12.2024 16:00H</span></div>
  <div class="profile-side">
    <svg style="top:22px" width="16" height="16" viewBox="0 0 16 16"><circle cx="7" cy="7" r="5" fill="none" stroke="#5c35f2" stroke-width="2"/><line x1="10.5" y1="10.5" x2="15" y2="15" stroke="#5c35f2" stroke-width="2"/></svg>
    <svg style="top:66px" width="16" height="16" viewBox="0 0 16 16"><rect x="1" y="2" width="14" height="12" fill="none" stroke="#5c35f2" stroke-width="2"/><line x1="1" y1="7" x2="15" y2="7" stroke="#5c35f2" stroke-width="1.5"/><line x1="6" y1="2" x2="6" y2="14" stroke="#5c35f2" stroke-width="1.5"/></svg>
    <svg style="top:102px" width="16" height="16" viewBox="0 0 16 16"><path d="M8 2 L8 10 M4 6 L8 2 L12 6 M2 11 V14 H14 V11" fill="none" stroke="#5c35f2" stroke-width="2"/></svg>
    <svg style="top:140px" width="16" height="16" viewBox="0 0 16 16"><rect x="2" y="3" width="12" height="12" rx="1" fill="#5c35f2"/><rect x="4" y="1" width="2" height="4" fill="#5c35f2"/><rect x="10" y="1" width="2" height="4" fill="#5c35f2"/></svg>
    <svg style="top:180px" width="20" height="20" viewBox="0 0 20 20"><circle cx="13" cy="7" r="4.5" fill="#5c35f2"/><line x1="10" y1="10" x2="3" y2="17" stroke="#5c35f2" stroke-width="3"/></svg>
    <svg style="top:222px" width="20" height="20" viewBox="0 0 20 20"><path d="M10 2 L19 6 L10 10 L1 6 Z M1 10 L10 14 L19 10 M1 14 L10 18 L19 14" fill="none" stroke="#5c35f2" stroke-width="2"/></svg>
  </div>
  <div class="profile-foot">
    <span class="pf-k" style="left:26px">VAPORN LEVEL</span><span class="pf-v" style="left:134px">179</span>
    <span class="pf-k" style="left:196px">ACCOUNT AGE</span><span class="pf-v" style="left:305px">15</span>
    <span class="pf-k" style="left:365px">PERFECT GAMES</span><span class="pf-v" style="left:490px">87</span>
    <svg class="abs" style="left:549px;top:20px" width="30" height="18" viewBox="0 0 30 18"><rect width="30" height="6" fill="#000"/><rect y="6" width="30" height="6" fill="#dd0000"/><rect y="12" width="30" height="6" fill="#ffce00"/></svg>
    <span class="pf-k" style="left:834px">USER NAME</span>
    <svg class="abs" style="left:929px;top:19px" width="16" height="16" viewBox="0 0 16 16"><circle cx="8" cy="8" r="8" fill="#5c35f2"/><circle cx="8" cy="6" r="2.6" fill="#0d0533"/><path d="M3.5 13 Q8 8.5 12.5 13" fill="#0d0533"/></svg>
  </div>
</section>

<div class="friend" style="left:115px" role="img" aria-label="Friend avatar"></div>
<div class="friend" style="left:271px" role="img" aria-label="Friend avatar"></div>
<div class="friend" style="left:427px" role="img" aria-label="Friend avatar"></div>
<div class="friend" style="left:585px" role="img" aria-label="Friend avatar"></div>
<div class="friend" style="left:741px" role="img" aria-label="Friend avatar"></div>
<div class="friend" style="left:898px" role="img" aria-label="Friend avatar"></div>
<svg class="abs" style="left:1059px;top:1508px" width="16" height="24" viewBox="0 0 16 24"><path d="M3 2 L13 12 L3 22" fill="none" stroke="#5c35f2" stroke-width="3"/></svg>

<div class="section-title" style="top:1772px">STATISTICS</div>
<div class="stat-tile" style="left:102px;top:1828px"><div class="label">Game</div><div class="num">251966</div>
  <svg style="right:34px;top:66px" width="48" height="28" viewBox="0 0 48 28"><rect x="0" y="2" width="48" height="24" rx="12" fill="#6f4bff"/><rect x="9" y="12" width="12" height="4" fill="#2c14a6"/><rect x="13" y="8" width="4" height="12" fill="#2c14a6"/><circle cx="33" cy="11" r="2.5" fill="#2c14a6"/><circle cx="38" cy="16" r="2.5" fill="#2c14a6"/></svg></div>
<div class="stat-tile" style="left:442px;top:1828px"><div class="label">Game achievements</div><div class="num">2692707</div>
  <svg style="right:34px;top:58px" width="28" height="40" viewBox="0 0 28 40"><circle cx="14" cy="13" r="10" fill="none" stroke="#6f4bff" stroke-width="5"/><path d="M6 21 L4 38 L14 32 L24 38 L22 21" fill="#6f4bff"/></svg></div>
<div class="stat-tile" style="left:779px;top:1828px"><div class="label">Game stats</div><div class="num">339284</div>
  <svg style="right:26px;top:62px" width="40" height="32" viewBox="0 0 40 32"><path d="M2 0 V30 H40" fill="none" stroke="#6f4bff" stroke-width="4"/><path d="M7 28 L7 14 L16 6 L24 16 L30 10 L38 20 L38 28 Z" fill="#6f4bff"/></svg></div>

<div class="stat-tile" style="left:102px;top:1968px"><div class="label">Playtime records</div><div class="num">3271530</div>
  <svg style="right:26px;top:56px" width="40" height="40" viewBox="0 0 40 40"><circle cx="20" cy="20" r="18" fill="#6f4bff"/><path d="M20 9 V21 L27 26" fill="none" stroke="#2c14a6" stroke-width="4"/></svg></div>
<div class="stat-tile" style="left:442px;top:1968px"><div class="label">Public profiles</div><div class="num">1033</div>
  <svg style="right:16px;top:60px" width="50" height="34" viewBox="0 0 50 34"><circle cx="25" cy="9" r="7" fill="#6f4bff"/><path d="M12 33 Q25 12 38 33 Z" fill="#6f4bff"/><circle cx="10" cy="13" r="5" fill="#6f4bff"/><circle cx="40" cy="13" r="5" fill="#6f4bff"/><path d="M1 30 Q8 18 16 26 L14 30 Z M49 30 Q42 18 34 26 L36 30 Z" fill="#6f4bff"/></svg></div>
<div class="stat-tile" style="left:779px;top:1968px"><div class="label">User achievements</div><div class="num">21087125</div>
  <svg style="right:34px;top:58px" width="28" height="40" viewBox="0 0 28 40"><circle cx="14" cy="13" r="10" fill="none" stroke="#6f4bff" stroke-width="5"/><path d="M6 21 L4 38 L14 32 L24 38 L22 21" fill="#6f4bff"/></svg></div>

<div class="stat-tile" style="left:102px;top:2112px"><div class="label">User stats</div><div class="num">2552885</div>
  <svg style="right:24px;top:60px" width="32" height="34" viewBox="0 0 32 34"><rect width="32" height="34" rx="2" fill="#6f4bff"/><rect x="7" y="18" width="4" height="10" fill="#2c14a6"/><rect x="14" y="8" width="4" height="20" fill="#2c14a6"/><rect x="21" y="14" width="4" height="14" fill="#2c14a6"/></svg></div>
<div class="stat-tile" style="left:442px;top:2112px"><div class="label">Owned games</div><div class="num">2276964</div>
  <svg style="right:16px;top:64px" width="48" height="28" viewBox="0 0 48 28"><rect x="0" y="2" width="48" height="24" rx="12" fill="#6f4bff"/><rect x="9" y="12" width="12" height="4" fill="#2c14a6"/><rect x="13" y="8" width="4" height="12" fill="#2c14a6"/><circle cx="33" cy="11" r="2.5" fill="#2c14a6"/><circle cx="38" cy="16" r="2.5" fill="#2c14a6"/></svg></div>
<div class="stat-tile" style="left:779px;top:2112px"><div class="label" style="top:20px">Years</div><div class="num" style="top:48px">2932</div><div class="sub">8 months 1 day 19 hours 43 minutes</div>
  <svg style="right:30px;top:36px" width="34" height="38" viewBox="0 0 34 38"><rect y="5" width="34" height="33" rx="3" fill="#6f4bff"/><rect x="7" y="0" width="5" height="9" fill="#6f4bff"/><rect x="22" y="0" width="5" height="9" fill="#6f4bff"/><rect x="0" y="13" width="34" height="2" fill="#2c14a6"/></svg></div>

<div class="section-title" style="top:2390px">GAMES</div>
<div class="game" style="left:143px;top:2482px;background:linear-gradient(160deg,#3b22c8,#5a3af0)" role="img" aria-label="Cargo Haul Odyssey 2 cover art">Cargo Haul Odyssey 2</div>
<div class="game" style="left:332px;top:2482px;background:linear-gradient(180deg,#7d8fa6,#4d5a5c 50%,#2d3036)" role="img" aria-label="Frontier Rig Journeys cover art">Frontier Rig Journeys</div>
<div class="game" style="left:520px;top:2482px;background:linear-gradient(160deg,#2e1aa8,#4d32e0)" role="img" aria-label="Leave the Chamber cover art">Leave the Chamber</div>
<div class="game" style="left:708px;top:2482px;background:linear-gradient(160deg,#2a1590,#5a2fd0)" role="img" aria-label="Hollow Manor 2 cover art">Hollow Manor 2</div>
<div class="game" style="left:896px;top:2482px;background:linear-gradient(160deg,#4a2bd8,#6a3ef5)" role="img" aria-label="Breakout 2091 cover art">Breakout 2091</div>
<div class="game" style="left:143px;top:2692px;background:linear-gradient(160deg,#3b22b8,#5a3cf0)" role="img" aria-label="Tiny Realm cover art">Tiny Realm</div>
<div class="game" style="left:332px;top:2692px;background:linear-gradient(160deg,#3a1eb0,#5530e6)" role="img" aria-label="Twig Sprout Quests cover art">Twig Sprout Quests</div>
<div class="game" style="left:520px;top:2692px;background:linear-gradient(180deg,#3b26c0,#2c1a98)" role="img" aria-label="Dwellhouse cover art">Dwellhouse</div>
<div class="game" style="left:708px;top:2692px;background:linear-gradient(180deg,#6a38e0,#3b1ab0)" role="img" aria-label="Visitors of the Lunar Rim cover art">Visitors of the Lunar Rim</div>
<div class="game" style="left:896px;top:2692px;background:linear-gradient(160deg,#2c1aa0,#4a3ae8)" role="img" aria-label="Block the Leaper cover art">Block the Leaper</div>

<svg class="abs" style="left:577px;top:2918px" width="46" height="50" viewBox="0 0 46 50"><circle cx="23" cy="4" r="3" fill="#5c35f2"/><circle cx="10" cy="10" r="3" fill="#5c35f2"/><circle cx="36" cy="10" r="3" fill="#6f4bff"/><circle cx="10" cy="38" r="3" fill="#5c35f2"/><circle cx="23" cy="44" r="3" fill="#5c35f2"/><circle cx="36" cy="38" r="3" fill="#5c35f2"/></svg>
<div class="loading">LOADING</div>

<footer>
  <div class="footer-glow"></div>
  <div class="foot-brand"><div class="brand-name">PLAYTALLY</div><div class="brand-tag">PLAYTALLYCOLLECTIVE</div></div>
  <nav class="foot-nav"><span class="active">HOME</span><span>VAPORN</span><span>GAMES</span><span>ABOUT</span></nav>
  <div class="social"><span>Friendwall</span><span>Chirp</span><span>Snapgrid</span></div>
  <div class="copyright">© 2024 | WWW.PLAYTALLY.EXAMPLE</div>
  <div class="version">M1</div>
</footer>

</body>
</html>
```